Design a New Business Card for Our Company

We are looking for fresh, unique, and a modern business card that reflects our roots as digital marketing agency focused on SEM.

Industry/Entity Type

Marketing

Contact Information for Business Card

looking for very unique out of the box designs. clean and modern that compliments our logo

Requirements
Must have
• colors should match our logo
• Front should have name, address, email, and phone/fax of the person, phone/fax are the same number
• back should have our url

```html
<!DOCTYPE html>
<html lang="en">
<head>
<meta charset="utf-8">
<title>Brightwave Business Card</title>
<link rel="stylesheet" href="https://fonts.googleapis.com/css2?family=Source+Sans+3:wght@400;600;700&display=swap">
<style>
  :root {
    --stage: #000000;
    --front-top: #6399d3;
    --front-bottom: #5a92cf;
    --back-top: #b9b9b9;
    --back-bottom: #aeaeae;
    --ink: #ffffff;
  }
  * { margin: 0; padding: 0; box-sizing: border-box; }
  html, body {
    width: 1200px; height: 900px; overflow: hidden;
    background: var(--stage);
    font-family: "Source Sans 3", "Myriad Pro", Arial, sans-serif;
    color: var(--ink);
  }
  .stage { position: relative; width: 1200px; height: 900px; }
  .card { position: absolute; top: 275px; width: 477px; height: 294px; overflow: hidden; }
  .card-front {
    left: 116px;
    background: linear-gradient(180deg, var(--front-top), var(--front-bottom));
    border-radius: 0 56px 0 56px;
  }
  .card-back {
    left: 622px;
    background: linear-gradient(180deg, var(--back-top), var(--back-bottom));
    border-radius: 56px 0 56px 0;
  }
  .brand {
    position: absolute; display: flex; align-items: center; gap: 10px;
    font-weight: 700; letter-spacing: -1px; line-height: 1;
  }
  .brand-dot { width: 30px; height: 30px; border-radius: 50%; background: var(--ink); flex: none; }
  .card-front .brand { right: 26px; top: 46px; font-size: 50px; }
  .card-back .brand { right: 48px; top: 186px; font-size: 54px; }
  .holder { position: absolute; left: 27px; top: 128px; }
  .holder-name { font-size: 18px; font-weight: 600; line-height: 1.1; }
  .holder-role { font-size: 13.5px; line-height: 1.2; }
  .divider { position: absolute; left: 0; right: 0; top: 175px; height: 1.5px; background: var(--ink); }
  .contacts {
    position: absolute; right: 26px; top: 182px;
    list-style: none; text-align: right; font-size: 13.5px;
  }
  .contacts li { display: flex; justify-content: flex-end; align-items: center; gap: 6px; height: 20.5px; }
  .contacts svg { width: 10px; height: 10px; fill: var(--ink); }
  .contacts .address { padding-right: 0; margin-top: 1px; }
</style>
</head>
<body>
<main class="stage">
  <section class="card card-front" aria-label="Card front">
    <div class="brand"><span class="brand-dot"></span>brightwave</div>
    <div class="holder">
      <p class="holder-name">Daniel Harrow</p>
      <p class="holder-role">Managing Director</p>
    </div>
    <div class="divider"></div>
    <ul class="contacts">
      <li>(021)-555-0147
        <svg viewBox="0 0 10 10" aria-hidden="true"><path d="M2 0.5 L3.6 2.6 L2.7 3.6 Q3.8 5.9 6.3 7.2 L7.3 6.3 L9.5 7.9 L8.4 9.5 Q3.5 9.2 0.5 1.7 Z"/></svg></li>
      <li>021-555-0148
        <svg viewBox="0 0 10 10" aria-hidden="true"><path d="M2.5 0.5 H7.5 V3 H9.5 V9.5 H0.5 V3 H2.5 Z M3.5 1.5 V3 H6.5 V1.5 Z M2 5 V6 H8 V5 Z M2 7 V8 H8 V7 Z" fill-rule="evenodd"/></svg></li>
      <li>hello@brightwave.co
        <svg viewBox="0 0 10 10" aria-hidden="true"><path d="M0.5 2 H9.5 V8.5 H0.5 Z M1 2.6 L5 5.6 L9 2.6 Z" fill-rule="evenodd"/></svg></li>
      <li class="address">12345, Address Goes Here Country Name, 123456</li>
    </ul>
  </section>
  <section class="card card-back" aria-label="Card back">
    <div class="brand">brightwave</div>
  </section>
</main>
</body>
</html>
```